Homeowners Insurance Provider Website

We are selling homeowners insurance policy / tenants Policy/Flood Insurance in USA in few states and planning expand nationally.

Our target audience are two folds: Customers (Buy policies) and Insurance Agents who wants to work with us to sell our policies to customers. But website should focus 80% on customers and 20% on agents. So, more customer focused user experience. Please note that there is no direct buy option for customers. They always go through insurance agents.

Customer focused, educational that makes buyer journey easy. We don’t want to come off as trying sell something as there is no direct sales involved from website.

Target Market(s)

Homeowners in USA and Insurance agent who sells these insurance.

Industry/Entity Type

Insurance

Number of Pages Required

4 page

Font styles to use
Other font styles liked:
• Open to suggestions

Colors

Designer to choose colors to be used in the design.

Requirements
Must have
• Three most important things: Trustworthy, Authentic, Simple
• Please use colors form logo and grays
• We like: www.hollowmere.com
• https://www.quillfenbrook.com/
• We need Agent Look up tool on home page similar to what is shown on example sites.
• Design:
• Home Page - Open to Ideas
• Insurance (Products) Landing Page - Info similar to: https://www.quillfenbrook.com/insurance/
• Agents Page - https://www.quillfenbrook.com/agents/
• Claims Page - Information similar to: https://www.quillfenbrook.com/claims-center/
• Site Navigation:
• Home
• Insurance
• Claims
• Agents
• About Us
• Contact Us
Nice to have
• Elegant, minimal and clean design that reflects trust and authenticity.
Should not have
• Slider or rotating images - prefer flat design. Not over powering design.

```html
<!DOCTYPE html>
<html lang="en">
<head>
<meta charset="utf-8">
<title>Hearthline Insurance Co. — Home</title>
<link href="https://fonts.googleapis.com/css2?family=Open+Sans:wght@400;600;700;800&family=Raleway:wght@400;500;600&display=swap" rel="stylesheet">
<style>
:root{
  --navy:#233b7d;
  --navy-dark:#1b2c5f;
  --red:#e1262d;
  --red-bright:#ee2a31;
  --ink:#222;
  --gray-text:#555;
  --gray-line:#cfd2d8;
  --gray-bg:#f4f4f5;
  --field:#ececee;
  --footer:#1e1e1e;
  --white:#fff;
}
*{box-sizing:border-box;margin:0;padding:0}
html,body{width:1200px;height:2903px;overflow:hidden}
body{font-family:'Raleway',sans-serif;color:var(--ink);background:var(--white)}
section,header,footer{position:relative;width:1200px}
.abs{position:absolute}
.btn{position:absolute;display:flex;align-items:center;justify-content:center;font-family:'Open Sans',sans-serif;font-size:13px;font-weight:600;text-transform:uppercase;color:var(--white);letter-spacing:.3px}
.btn-red{background:var(--red)}
.btn-navy{background:var(--navy)}
.btn-white{background:var(--white);color:var(--red)}

/* hero */
.hero{height:548px;overflow:hidden}
.hero-photo{position:absolute;inset:0;background:linear-gradient(100deg,#1c2a45 0%,#2d3e5e 45%,#4a5974 70%,#2b3852 100%)}
.nav{position:absolute;left:141px;top:35px;width:918px;height:85px;background:rgba(236,238,242,.93);display:flex;align-items:center;padding:0 12px 0 14px}
.brand{display:flex;align-items:center;gap:12px}
.brand-mark{width:40px;height:40px;background:var(--navy)}
.brand-name{font-family:'Open Sans',sans-serif;font-weight:700;font-size:24px;color:var(--navy);line-height:1}
.nav-links{margin-left:auto;display:flex;align-items:center;gap:17px;font-family:'Open Sans',sans-serif;font-size:13px;color:#2a2a2a}
.nav-links .active{color:var(--red)}
.nav-links .quote{background:var(--navy);color:var(--white);padding:8px 9px}
.hero-box{position:absolute;left:141px;top:269px;width:492px;height:143px;background:rgba(236,238,242,.93);border-radius:6px;padding:18px 18px}
.hero-title{font-family:'Open Sans',sans-serif;font-weight:700;font-size:25px;line-height:32px;color:#1c1c2a;text-transform:uppercase}
.hero .btn{left:163px;top:397px;width:106px;height:30px}

/* services + about */
.intro{height:509px}
.service{position:absolute;top:-96px;width:200px;text-align:center}
.service-ring{width:174px;height:174px;margin:0 auto;border-radius:50%;background:linear-gradient(180deg,#c5c8cf 50%,transparent 50%);padding:9px}
.service-circle{width:156px;height:156px;border-radius:50%;background:var(--white);display:flex;align-items:center;justify-content:center;box-shadow:0 1px 3px rgba(0,0,0,.08)}
.service-label{margin-top:18px;font-family:'Open Sans',sans-serif;font-weight:600;font-size:15px;line-height:21px;color:var(--red);text-transform:uppercase}
.section-title{font-family:'Open Sans',sans-serif;font-weight:600;font-size:26px;letter-spacing:.5px;color:#1a1a1a;text-transform:uppercase}
.about-title{left:141px;top:174px}
.about-rule{left:141px;top:239px;width:618px;height:1px;background:var(--gray-line)}
.about-rule::before{content:"";position:absolute;left:0;top:-2px;width:62px;height:4px;background:var(--navy)}
.about-text{left:145px;top:263px;width:614px;font-size:13px;line-height:23px;color:var(--gray-text)}
.intro .btn{left:141px;top:423px;width:130px;height:29px}
.quote-card{left:819px;top:172px;width:240px;height:282px;background:#f0f0f2;border:1px solid #dcdde1}
.quote-head{height:37px;background:var(--navy);color:var(--white);font-family:'Open Sans',sans-serif;font-weight:600;font-size:21px;display:flex;align-items:center;justify-content:center}
.quote-form{padding:13px 14px}
.field{height:30px;background:var(--field);border:1px solid #d8d9dd;margin-bottom:7px;font-size:11px;color:#888;padding:8px 10px}
.field.tall{height:52px}
.quote-form .submit{height:31px;background:var(--navy);color:var(--white);font-family:'Open Sans',sans-serif;font-size:12px;font-weight:600;display:flex;align-items:center;justify-content:center;margin-top:12px}

/* audience split */
.split{height:328px;display:flex}
.split-half{width:600px;height:328px;position:relative;color:var(--white)}
.split-half.customers{background:var(--red-bright)}
.split-half.agents{background:var(--navy)}
.split h3{position:absolute;top:52px;font-family:'Open Sans',sans-serif;font-size:19px;font-weight:700}
.split p{position:absolute;top:85px;width:355px;font-size:13px;line-height:20.5px}
.customers h3,.customers p{left:141px}
.agents h3{right:141px}
.agents p{right:141px;text-align:right}
.customers .btn{left:141px;top:244px;width:130px;height:29px}
.agents .btn{right:141px;top:244px;width:130px;height:29px}
.split-seal{left:525px;top:89px;width:150px;height:150px;border-radius:50%;background:var(--white);border:10px solid var(--navy)}

/* insurance */
.insurance{height:627px;background:var(--gray-bg)}
.center-title{position:absolute;left:0;width:1200px;text-align:center}
.insurance .center-title{top:42px}
.center-rule{position:absolute;left:292px;width:616px;height:1px;background:#a7aab1}
.center-rule::before{content:"";position:absolute;left:277px;top:-2px;width:62px;height:4px;background:var(--navy)}
.insurance .center-rule{top:105px}
.cards{position:absolute;left:141px;top:157px;width:918px;height:414px;display:flex}
.card{position:relative;width:306px;height:414px;overflow:hidden;color:var(--white);text-align:center}
.card-photo{position:absolute;inset:0}
.card.home .card-photo{background:linear-gradient(180deg,#d9d7d2 0%,#a79f95 45%,#2a2a2c 80%,#151515 100%)}
.card.tenant .card-photo{background:linear-gradient(180deg,#c9a98e 0%,#8a6b58 40%,#3d3026 100%)}
.card.flood .card-photo{background:linear-gradient(180deg,#6f8f4a 0%,#7d4a3a 45%,#2a2320 80%,#141414 100%)}
.card.tenant .overlay{position:absolute;left:0;right:0;top:200px;bottom:0;background:rgba(35,59,125,.88)}
.card h4{position:absolute;left:0;right:0;top:236px;font-family:'Open Sans',sans-serif;font-weight:600;font-size:20px}
.card.tenant h4{top:224px}
.card h4::after{content:"";display:block;width:50px;height:2px;background:var(--red);margin:9px auto 0}
.card p{position:absolute;left:22px;right:22px;top:286px;font-size:11.5px;line-height:19px;color:#e8e8e8}
.card.tenant p{top:274px}
.card .btn{top:358px;height:29px;font-size:12px}
.card.tenant .btn{top:346px}
.card .btn.q{left:30px;width:108px}
.card .btn.r{left:146px;width:132px}

/* find an agent */
.agent-find{height:293px;background:var(--navy-dark);color:var(--white)}
.agent-find .center-title{top:47px;color:var(--white)}
.agent-find .center-rule{top:102px;left:541px;width:118px;background:transparent}
.agent-find .center-rule::before{left:28px;width:62px;height:3px;background:#8fa0d0}
.agent-text{position:absolute;left:290px;width:620px;top:131px;text-align:center;font-size:13px;line-height:23px;color:#e6e9f2}
.search{left:441px;top:220px;width:153px;height:29px;background:var(--white);color:#777;font-size:12px;padding:7px 6px}
.agent-find .btn{left:604px;top:220px;width:156px;height:29px}

/* claims + contact */
.claims{height:313px}
.claim-kicker{left:130px;width:300px;top:50px;text-align:center;font-family:'Open Sans',sans-serif;font-weight:600;font-size:26px;color:var(--navy-dark)}
.claim-big{left:130px;width:300px;top:84px;text-align:center;font-family:'Open Sans',sans-serif;font-weight:800;font-size:54px;line-height:64px;color:var(--red)}
.claim-text{left:150px;width:260px;top:158px;text-align:center;font-size:14px;line-height:23px;color:var(--navy-dark);font-weight:500}
.claims .login{left:238px;top:227px;width:85px;height:29px}
.divider{left:433px;top:52px;width:1px;height:218px;background:#d4d6da}
.contact-title{left:484px;top:46px}
.contact-rule{left:484px;top:97px;width:526px;height:1px;background:var(--gray-line)}
.contact-rule::before{content:"";position:absolute;left:0;top:-2px;width:36px;height:4px;background:var(--navy)}
.contact-hint{left:484px;top:112px;font-size:11px;color:#555}
.cfield{position:absolute;width:257px;height:31px;border:1px solid #cfd1d6;font-size:11px;color:#777;padding:9px 10px;background:var(--white)}
.claims .submit{left:484px;top:227px;width:86px;height:28px}

/* footer */
.footer{height:248px;background:var(--footer);color:#cfcfcf}
.fcol{position:absolute;top:40px}
.fcol h5{font-family:'Open Sans',sans-serif;font-weight:400;font-size:16px;color:var(--white);padding-bottom:9px;border-bottom:1px solid #444}
.quick{left:159px;width:102px}
.quick ul{list-style:none;margin-top:11px;font-size:11px;line-height:22px}
.quick li::before{content:"›";margin-right:8px;color:#888}
.quick li.current{color:#3c5aa8}
.contact-col{left:339px;width:185px}
.contact-col .org{margin-top:13px;font-size:12px;color:var(--white);font-weight:500}
.contact-col .addr{font-size:11px;line-height:17px;margin-top:3px}
.contact-line{display:flex;align-items:center;gap:10px;font-size:13px}
.news{left:623px;width:215px}
.news p{margin-top:14px;font-size:11px;line-height:18px}
.news .email{margin-top:12px;width:172px;height:29px;background:#3a3a3a;font-size:11px;color:#ddd;padding:8px 9px}
.news .sub{margin-top:10px;width:92px;height:27px;background:var(--red);color:var(--white);font-size:12px;display:flex;align-items:center;justify-content:center}
.footer-brand{left:895px;top:110px;width:170px;text-align:center;font-family:'Open Sans',sans-serif;font-weight:600;font-size:18px;color:#bdbdbd}
.bar{height:37px;background:var(--navy-dark);color:var(--white);font-family:'Open Sans',sans-serif;font-size:12px;font-weight:600}
.bar .copy{left:141px;top:11px}
.social{right:141px;top:8px;display:flex;gap:6px}
.social span{width:21px;height:21px;background:#2f62b5;display:block;border:1px solid #6d8fd0}
</style>
</head>
<body>

<header class="hero">
  <div class="hero-photo" role="img" aria-label="Photograph of a businessman's hands sheltering a small model house with a red roof"></div>
  <nav class="nav">
    <div class="brand"><span class="brand-mark"></span><span class="brand-name">Hearthline Insurance Co.</span></div>
    <div class="nav-links">
      <span class="active">Home</span><span>About Us</span><span>Insurance</span><span>Agents</span><span>Claims</span><span>Contact Us</span><span class="quote">Get a quote</span>
    </div>
  </nav>
  <div class="hero-box">
    <h1 class="hero-title">Get homeowners insurance policy / tenants policy/ flood insurance in USA</h1>
  </div>
  <a class="btn btn-red">Read more</a>
</header>

<section class="intro">
  <div class="service" style="left:210px">
    <div class="service-ring"><div class="service-circle">
      <svg width="60" height="60" viewBox="0 0 60 60"><path d="M10 30 L30 12 L50 30" fill="none" stroke="#e1262d" stroke-width="4"/><rect x="17" y="28" width="26" height="20" fill="#e1262d"/><text x="30" y="44" fill="#fff" font-family="Open Sans" font-weight="700" font-size="13" text-anchor="middle">%</text><path d="M6 52 Q20 44 32 52 L54 46" fill="none" stroke="#e1262d" stroke-width="3"/></svg>
    </div></div>
    <div class="service-label">Homeowners<br>policy</div>
  </div>
  <div class="service" style="left:496px">
    <div class="service-ring"><div class="service-circle">
      <svg width="60" height="60" viewBox="0 0 60 60"><path d="M6 28 L30 8 L54 28 L54 52 L6 52 Z" fill="#e1262d"/><circle cx="23" cy="30" r="5" fill="#fff"/><circle cx="37" cy="30" r="5" fill="#fff"/><rect x="17" y="37" width="12" height="15" fill="#fff"/><rect x="31" y="37" width="12" height="15" fill="#fff"/></svg>
    </div></div>
    <div class="service-label" style="margin-top:29px">Tenants policy</div>
  </div>
  <div class="service" style="left:782px">
    <div class="service-ring"><div class="service-circle">
      <svg width="60" height="60" viewBox="0 0 60 60"><path d="M10 28 L30 12 L50 28 L50 40 L10 40 Z" fill="#e1262d"/><rect x="26" y="30" width="8" height="10" fill="#fff"/><path d="M6 46 q6 -5 12 0 t12 0 t12 0 t12 0" fill="none" stroke="#e1262d" stroke-width="3"/><path d="M6 53 q6 -5 12 0 t12 0 t12 0 t12 0" fill="none" stroke="#e1262d" stroke-width="3"/></svg>
    </div></div>
    <div class="service-label" style="margin-top:29px">Flood insurance</div>
  </div>

  <h2 class="section-title abs about-title">About Us</h2>
  <div class="abs about-rule"></div>
  <p class="abs about-text">Lorem ipsum dolor sit amet, consectetuer adipiscing elit, sed diam nonummy nibh euismod tincidunt ut laoreet dolore magna aliquam erat volutpat. Ut wisi enim ad minim veniam, quis nostrud exerci tation ullamcorper suscipit lobortis nisl ut aliquip ex ea commodo consequat. Duis autem vel eum iriure dolor in hendrerit in vulputate velit esse molestie consequat, vel illum dolore eu feugiat nulla facilisis at vero eros et accumsan et iusto odio dignissim qui blandit praesent luptatum zzril delenit augue duis dolore te feugait nulla facilisi.</p>
  <a class="btn btn-navy">Read more</a>

  <aside class="abs quote-card">
    <div class="quote-head">Get A Quote</div>
    <div class="quote-form">
      <div class="field">Name</div>
      <div class="field">Email</div>
      <div class="field">Subject</div>
      <div class="field tall">Message</div>
      <div class="submit">SUBMIT</div>
    </div>
  </aside>
</section>

<section class="split">
  <div class="split-half customers">
    <h3>Customers</h3>
    <p>Lorem ipsum dolor sit amet, consectetuer adipiscing elit, sed diam nonummy nibh euismod tincidunt ut laoreet dolore magna aliquam erat volutpat. Ut wisi enim ad minim veniam, quis nostrud exerci tation ullamcorper suscipit lobortis nisl ut aliquip ex ea commodo consequat. Duis autem vel eum iriure dolor in hendrerit in vulputate velit esse molestie consequat.</p>
    <a class="btn btn-navy">Learn more</a>
  </div>
  <div class="split-half agents">
    <h3>Agents</h3>
    <p>Lorem ipsum dolor sit amet, consectetuer adipiscing elit, sed diam nonummy nibh euismod tincidunt ut laoreet dolore magna aliquam erat volutpat. Ut wisi enim ad minim veniam, quis nostrud exerci tation ullamcorper suscipit lobortis nisl ut aliquip ex ea commodo consequat. Duis autem vel eum iriure dolor in hendrerit in vulputate velit esse molestie consequat.</p>
    <a class="btn btn-red">Learn more</a>
  </div>
  <div class="abs split-seal"></div>
</section>

<section class="insurance">
  <h2 class="section-title center-title">Insurance</h2>
  <div class="center-rule"></div>
  <div class="cards">
    <article class="card home">
      <div class="card-photo" role="img" aria-label="Photograph of a couple looking around the bright interior of a new home"></div>
      <h4>Homeowner Policy</h4>
      <p>Lorem ipsum dolor sit amet, consectetuer adipiscing elit, sed diam nonummy nibh euismod tincidunt ut laoreet dolore magna aliquam erat volutpat.</p>
      <a class="btn btn-red q">Quote →</a><a class="btn btn-navy r">Read more →</a>
    </article>
    <article class="card tenant">
      <div class="card-photo" role="img" aria-label="Photograph of smiling tenants reviewing papers together"></div>
      <div class="overlay"></div>
      <h4>Tenant Policy</h4>
      <p>Lorem ipsum dolor sit amet, consectetuer adipiscing elit, sed diam nonummy nibh euismod tincidunt ut laoreet dolore magna aliquam erat volutpat.</p>
      <a class="btn btn-red q">Quote →</a><a class="btn btn-white r">Read more →</a>
    </article>
    <article class="card flood">
      <div class="card-photo" role="img" aria-label="Photograph of a red wooden house tilted by flood damage among trees"></div>
      <h4>Flood Policy</h4>
      <p>Lorem ipsum dolor sit amet, consectetuer adipiscing elit, sed diam nonummy nibh euismod tincidunt ut laoreet dolore magna aliquam erat volutpat.</p>
      <a class="btn btn-red q">Quote →</a><a class="btn btn-navy r">Read more →</a>
    </article>
  </div>
</section>

<section class="agent-find">
  <h2 class="section-title center-title">Find An Agent</h2>
  <div class="center-rule"></div>
  <p class="agent-text">Lorem ipsum dolor sit amet, consectetuer adipiscing elit, sed diam nonummy nibh euismod tincidunt ut laoreet dolore magna aliquam erat volutpat. Ut wisi enim ad minim veniam, quis nostrud exerci tation ullamcorper suscipit lobortis nisl ut aliquip ex ea commodo consequat.</p>
  <div class="abs search">Search...</div>
  <a class="btn btn-red">Find an agent</a>
</section>

<section class="claims">
  <div class="abs claim-kicker">Report And Check</div>
  <div class="abs claim-big">A Claim</div>
  <p class="abs claim-text">Login To Report A Claim Or Check Your Claim Status.</p>
  <a class="btn btn-red login">Login</a>
  <div class="abs divider"></div>
  <h2 class="section-title abs contact-title">Contact Form</h2>
  <div class="abs contact-rule"></div>
  <div class="abs contact-hint">Please fill up bellow form</div>
  <div class="cfield" style="left:484px;top:133px">Name</div>
  <div class="cfield" style="left:753px;top:133px">Email</div>
  <div class="cfield" style="left:484px;top:178px">Phone</div>
  <div class="cfield" style="left:753px;top:178px">Message</div>
  <a class="btn btn-red submit">Submit</a>
</section>

<footer class="footer">
  <div class="fcol quick">
    <h5>Quick Links</h5>
    <ul><li class="current">Home</li><li>About Us</li><li>Insurance</li><li>Agents</li><li>Claims</li><li>Contact Us</li></ul>
  </div>
  <div class="fcol contact-col">
    <h5>Contact Detail</h5>
    <div class="org">Hearthline Insurance</div>
    <div class="addr">Lorem ipsum dolor sit amet, consectetuer adipiscing elit, sed do eiusmod</div>
    <div class="contact-line" style="margin-top:22px">
      <svg width="14" height="14" viewBox="0 0 24 24"><path d="M6.6 10.8a15 15 0 0 0 6.6 6.6l2.2-2.2a1 1 0 0 1 1-.25 11.4 11.4 0 0 0 3.6.57 1 1 0 0 1 1 1V20a1 1 0 0 1-1 1A17 17 0 0 1 3 4a1 1 0 0 1 1-1h3.5a1 1 0 0 1 1 1c0 1.25.2 2.45.57 3.57a1 1 0 0 1-.25 1z" fill="#3c5aa8"/></svg>
      <span>123.456.7890</span>
    </div>
    <div class="contact-line" style="margin-top:14px;font-size:11px">
      <svg width="14" height="11" viewBox="0 0 14 11"><rect width="14" height="11" fill="#3c5aa8"/><path d="M0 0 L7 6 L14 0" fill="none" stroke="#1e1e1e" stroke-width="1.3"/></svg>
      <span>info@hearthline.com</span>
    </div>
  </div>
  <div class="fcol news">
    <h5>Join Our Newsletter</h5>
    <p>Subscribe to our Newsletter to get the latest scoop right to your inbox</p>
    <div class="email">Enter Your Email</div>
    <div class="sub">Subscribe</div>
  </div>
  <div class="abs footer-brand">Hearthline Insurance Co.</div>
</footer>

<div class="bar" style="position:relative;width:1200px">
  <span class="abs copy">© 2018 Hearthlineinsurance. All Rights Reserved.</span>
  <div class="abs social"><span></span><span></span><span></span></div>
</div>

</body>
</html>
```